Verodex business card

Business card for sustainable investment company called "Verodex". Verodex is an exchange platform selling carbon credits between buyers and sellers. Carbon Credits are an environmental commodity for reducing global carbon emissions.

the card should obviously have our logo and the theme should be sustainability/environment mixed with a trading platform.

Contact Information for Business Card

Logo, Name, Title, Phone, Email

Colors
0054AA
0677BA
7BADD7
CADEEF
E8F1F8
0094D4
00A9DD
6FCCEA
C7EBF8
E9F6FB
00AB8E
00BBA5
67D7C9
C6EFE9
E9F9F6
59FF00
82FF00
B8FF75
E3FFCB
F4FFEA

```html
<!DOCTYPE html>
<html lang="en">
<head>
<meta charset="utf-8">
<title>Verodex business card</title>
<link href="https://fonts.googleapis.com/css2?family=Montserrat:wght@400;500;700&display=swap" rel="stylesheet">
<style>
  :root {
    --page-bg: #eceef1;
    --card-white: #ffffff;
    --navy: #1d2e4d;
    --sky: #35b8e8;
    --aqua-light: #6fcfe0;
    --aqua-mid: #33bdea;
    --royal: #4670b8;
    --text-dark: #1b1b1b;
  }
  * { margin: 0; padding: 0; box-sizing: border-box; }
  html, body {
    width: 1200px;
    height: 900px;
    overflow: hidden;
    background: var(--page-bg);
    font-family: "Montserrat", Arial, sans-serif;
  }
  .stage {
    position: relative;
    width: 1200px;
    height: 900px;
  }
  .card {
    position: absolute;
    left: 270px;
    width: 660px;
    height: 377px;
    border-radius: 4px;
    overflow: hidden;
    box-shadow: 0 6px 18px rgba(0, 0, 0, 0.12);
  }
  .card-front {
    top: 53px;
    background: linear-gradient(45deg, var(--aqua-light) 0%, var(--aqua-mid) 45%, var(--royal) 100%);
    display: flex;
    align-items: center;
    justify-content: center;
  }
  .front-brand {
    display: flex;
    align-items: center;
    gap: 22px;
  }
  .brand-square {
    width: 58px;
    height: 58px;
    background: var(--card-white);
    border-radius: 6px;
  }
  .front-brand .brand-name {
    color: var(--card-white);
    font-weight: 700;
    font-size: 66px;
    letter-spacing: 2px;
  }
  .card-back {
    top: 470px;
    background: var(--card-white);
  }
  .back-wave {
    position: absolute;
    inset: 0;
    width: 100%;
    height: 100%;
  }
  .back-brand {
    position: absolute;
    left: 70px;
    top: 56px;
    display: flex;
    align-items: center;
    gap: 20px;
  }
  .back-brand .brand-square {
    width: 54px;
    height: 54px;
    background: var(--sky);
  }
  .back-brand .brand-name {
    color: var(--navy);
    font-weight: 700;
    font-size: 60px;
    letter-spacing: 2px;
  }
  .identity {
    position: absolute;
    left: 70px;
    top: 150px;
    display: flex;
    align-items: center;
  }
  .person {
    text-align: right;
    padding-right: 16px;
  }
  .person-name {
    font-weight: 700;
    font-size: 21px;
    letter-spacing: 0.5px;
  }
  .person-name .first { color: var(--sky); }
  .person-name .last { color: var(--navy); }
  .person-title {
    font-weight: 400;
    font-size: 15px;
    color: var(--text-dark);
    margin-top: 2px;
  }
  .divider {
    width: 2px;
    height: 82px;
    background: var(--sky);
  }
  .contacts {
    list-style: none;
    padding-left: 16px;
  }
  .contacts li {
    display: flex;
    align-items: center;
    gap: 8px;
    font-size: 14px;
    color: var(--text-dark);
    line-height: 24px;
  }
  .contacts svg {
    width: 14px;
    height: 14px;
    flex: none;
  }
</style>
</head>
<body>
<main class="stage">

  <section class="card card-front" aria-label="Card front">
    <div class="front-brand">
      <span class="brand-square"></span>
      <span class="brand-name">VERODEX</span>
    </div>
  </section>

  <section class="card card-back" aria-label="Card back">
    <svg class="back-wave" viewBox="0 0 660 377" preserveAspectRatio="none" aria-hidden="true">
      <defs>
        <linearGradient id="waveFill" x1="0" y1="1" x2="1" y2="0">
          <stop offset="0" stop-color="#6fcfe0"/>
          <stop offset="0.45" stop-color="#33bdea"/>
          <stop offset="1" stop-color="#4670b8"/>
        </linearGradient>
      </defs>
      <path d="M190 377 C320 352 420 330 490 250 C555 175 600 140 660 128 L660 377 Z" fill="url(#waveFill)"/>
      <path d="M330 350 C420 330 470 285 515 220 C555 165 590 135 640 118" fill="none" stroke="#1d2e4d" stroke-width="4" stroke-linecap="round"/>
    </svg>

    <div class="back-brand">
      <span class="brand-square"></span>
      <span class="brand-name">VERODEX</span>
    </div>

    <div class="identity">
      <div class="person">
        <p class="person-name"><span class="first">MARCUS</span> <span class="last">VELLAN</span></p>
        <p class="person-title">Co-Founder</p>
      </div>
      <span class="divider"></span>
      <ul class="contacts">
        <li>
          <svg viewBox="0 0 16 16" aria-hidden="true"><path d="M3 1.5h3l1.2 3.3-1.8 1.2a9 9 0 0 0 4.6 4.6l1.2-1.8 3.3 1.2v3c0 .6-.5 1.1-1.1 1.1A12.9 12.9 0 0 1 1.9 2.6c0-.6.5-1.1 1.1-1.1z" fill="#35b8e8"/></svg>
          415-620-3187
        </li>
        <li>
          <svg viewBox="0 0 16 16" aria-hidden="true"><rect x="1" y="3" width="14" height="10" rx="1" fill="#35b8e8"/><path d="M1.5 3.8 8 9l6.5-5.2" fill="none" stroke="#ffffff" stroke-width="1.3"/></svg>
          info@verodex.com
        </li>
        <li>
          <svg viewBox="0 0 16 16" aria-hidden="true"><circle cx="8" cy="8" r="7" fill="#35b8e8"/><path d="M1 8h14M8 1c-2.5 2-2.5 12 0 14M8 1c2.5 2 2.5 12 0 14" fill="none" stroke="#ffffff" stroke-width="1"/></svg>
          www.verodex.com
        </li>
      </ul>
    </div>
  </section>

</main>
</body>
</html>
```